Trucking Company Website Design

We are working with a Trucking company in California. They provide trucking services for dirt, gravel, landscape bark, and landscape materials.

As you might imagine, there are no websites we could find for inspiration for trucking companies.

Thank you for taking the time to consider designing a website for us. We are web developers based in Stockton, CA, USA. Most of our projects go through the same process. Understanding this process may help you win a project with us. We custom-code all of our websites in-house. We don’t have any requirements as to what tools you use for your design, but we ask that you follow these guidelines.

IMAGES:
If you use any images or icons in the design, we ask that you have a link to the asset so we can purchase the image/icon. Most of the designs we submit do not have the customer’s images on them unless they have some great images. Be creative; show us the feeling you are trying to portray with your image choices. Use any royalty-free site you choose. We subscribe to Quillo and mainly use their images, but we can purchase images outside of Quillo. PLEASE NOTE: we will not submit designs to clients with watermarks on the images.

FONTS:
We ask that you identify the fonts you’re using in the design. This can be done in a message if you want. We typically use Varnex Fonts and Quillo Fonts.

CONTENT:
We're always open to different content and ideas. We often submit designs with stock images so the client can see our vision. We typically take pictures after the website launch to use their images with our vision. Lorem Ipsum is fine for paragraphs, but we ask that you make the Headers with correct English. We want to be able to show the vision and identify the sections of the website.

INSPIRATION:
We typically add a couple of links in the brief of websites we like to help you get started in your design.

REVISIONS:
We do not often ask for revisions of the designs unless we see something in the design that may not appeal to the client. If there are slight changes that we want to make, we do that in the development process.

FEEDBACK:
We rarely give feedback on designs during the design process. We are working on many website projects and do not have the time to provide feedback. We usually respond if your request is well thought out and asks specific questions, but a note asking “feedback, please” usually goes unanswered.

```html
<!DOCTYPE html>
<html lang="en">
<head>
<meta charset="utf-8">
<title>Ridgeline Haulage — Trucking Services</title>
<link rel="stylesheet" href="https://fonts.googleapis.com/css2?family=Saira:wght@600;700;800&family=Roboto:wght@400;500;700&display=swap">
<style>
:root{
  --red:#e31e24;
  --blue:#1f82bf;
  --blue-dark:#1b5f8f;
  --blue-pale:#d4e8f2;
  --ink:#141414;
  --text:#2b2b2b;
  --muted:#555;
  --light:#f3f3f3;
  --footer:#151515;
  --white:#fff;
}
*{box-sizing:border-box;margin:0;padding:0}
html,body{width:1200px;height:3603px;overflow:hidden}
body{position:relative;font-family:"Roboto",sans-serif;color:var(--text);background:var(--white)}
.abs{position:absolute}
.head-font{font-family:"Saira",sans-serif;font-weight:800;text-transform:uppercase}

/* top bar */
.topbar{left:0;top:0;width:1200px;height:44px;background:var(--red);color:var(--white);font-size:15px}
.topbar .item{position:absolute;top:13px;display:flex;align-items:center;gap:10px}
.topbar .dots{position:absolute;right:125px;top:14px;display:flex;gap:14px}
.topbar .dots span{width:13px;height:13px;border-radius:50%;background:var(--white);display:block}

/* header */
.header{left:0;top:44px;width:1200px;height:91px;background:var(--white)}
.brand{position:absolute;display:flex;align-items:center;gap:14px;font-family:"Saira",sans-serif;font-weight:800;font-size:30px;color:var(--blue);text-transform:uppercase;line-height:29px}
.brand .words{display:flex;flex-direction:column}
.brand .mark{width:30px;height:30px;background:var(--red)}
.header .brand{left:111px;top:16px}
.nav{position:absolute;top:34px;font-size:15px;color:var(--ink)}
.login{position:absolute;left:961px;top:21px;width:127px;height:48px;border-radius:24px;background:var(--blue);color:var(--white);font-family:"Saira",sans-serif;font-weight:700;font-size:15px;display:flex;align-items:center;justify-content:center;gap:10px}

/* hero */
.hero{left:0;top:135px;width:1200px;height:559px;overflow:hidden;background:linear-gradient(110deg,#b8322a 0%,#c9472a 45%,#d9762e 70%,#8a6a58 100%)}
.hero .overlay{position:absolute;inset:0}
.hero .welcome{left:110px;top:132px;color:var(--blue);font-size:20px}
.hero h1{left:110px;top:160px;color:var(--white);font-size:64px;line-height:71px;letter-spacing:1px}
.hero .cta{left:110px;top:322px;width:161px;height:53px;border-radius:27px;background:var(--white);color:var(--red);font-family:"Saira",sans-serif;font-weight:700;font-size:15px;display:flex;align-items:center;justify-content:center;text-transform:uppercase}

/* shared */
.section-title{width:1200px;left:0;text-align:center;color:var(--ink);font-size:36px}
.lead{left:240px;width:720px;text-align:center;font-size:15px;line-height:25px;color:var(--text)}

/* services */
.card{background:var(--white);box-shadow:0 2px 14px rgba(0,0,0,.07);text-align:center}
.card.active{background:var(--blue-pale);border:2px solid var(--blue-dark);box-shadow:none}
.card .icon{position:absolute;left:50%;top:38px;width:91px;height:91px;margin-left:-45px;border-radius:50%;background:var(--red);display:flex;align-items:center;justify-content:center}
.card.active .icon{background:var(--blue);box-shadow:0 0 0 7px #8fc2de}
.card h3{position:absolute;left:0;width:100%;font-family:"Saira",sans-serif;font-weight:700;font-size:20px;color:var(--ink);text-transform:uppercase;line-height:25px}
.card p{position:absolute;left:14px;right:14px;font-size:15px;line-height:28.5px;color:var(--text)}
.card .more{position:absolute;left:0;width:100%;font-family:"Saira",sans-serif;font-weight:700;font-size:14px;color:var(--blue-dark);text-transform:uppercase}

/* about */
.about-band{left:0;top:1376px;width:1200px;height:531px;background:var(--blue)}
.about h2{left:624px;top:1432px;color:var(--white);font-size:36px}
.about p{left:622px;top:1494px;width:476px;color:var(--white);font-size:15px;line-height:24px}
.btn-red{background:var(--red);color:var(--white);font-family:"Saira",sans-serif;font-weight:700;font-size:15px;display:flex;align-items:center;justify-content:center;text-transform:uppercase}

/* testimonials */
.quote{background:var(--white);box-shadow:0 2px 16px rgba(0,0,0,.07);width:407px;height:321px;top:2094px}
.quote .qmark{position:absolute;left:26px;top:28px;color:var(--red);font-family:"Saira",sans-serif;font-weight:800;font-size:56px;line-height:56px}
.quote h4{position:absolute;left:26px;top:80px;width:360px;font-family:"Saira",sans-serif;font-weight:700;font-size:26px;line-height:38px;color:var(--ink)}
.quote p{position:absolute;left:26px;top:162px;width:362px;font-size:15px;line-height:26px;color:var(--text)}
.quote .who{position:absolute;left:26px;top:244px;display:flex;gap:12px;align-items:center}
.quote .avatar{width:45px;height:45px;border-radius:50%;background:#b9c7d3;border:2px solid var(--blue)}
.quote .name{font-family:"Saira",sans-serif;font-weight:700;font-size:22px;color:var(--ink);line-height:24px}
.quote .role{font-size:15px;color:var(--text)}
.arrow{width:38px;height:38px;border-radius:50%;top:2247px;display:flex;align-items:center;justify-content:center}

/* contact */
.contact-bg{left:0;top:2505px;width:1200px;height:648px;background:var(--light)}
.field{background:var(--white);height:51px;top:2720px;width:315px;display:flex;align-items:center;gap:10px;padding-left:20px;font-size:15px;color:#666}
.field.message{top:2789px;left:110px;width:978px;height:171px;align-items:flex-start;padding-top:14px}

/* footer */
.footer{left:0;top:3153px;width:1200px;height:450px;background:var(--footer);color:var(--white)}
.footer h5{position:absolute;top:92px;font-family:"Saira",sans-serif;font-weight:700;font-size:21px;text-transform:uppercase}
.footer .links{position:absolute;left:396px;top:134px;list-style:none;font-size:15px;line-height:30px}
.footer .links li::before{content:"«";color:var(--blue);margin-right:8px}
.footer .small{font-size:12.5px;line-height:20px}
.social{position:absolute;top:200px;width:28px;height:28px;border-radius:50%;background:#2f2f2f}
.social.first{background:var(--red)}
</style>
</head>
<body>

<!-- top bar -->
<div class="abs topbar">
  <div class="item" style="left:122px">
    <svg width="15" height="15" viewBox="0 0 24 24" fill="#fff"><path d="M6.6 10.8a15.1 15.1 0 0 0 6.6 6.6l2.2-2.2a1 1 0 0 1 1-.25 11.4 11.4 0 0 0 3.6.57 1 1 0 0 1 1 1V20a1 1 0 0 1-1 1A17 17 0 0 1 3 4a1 1 0 0 1 1-1h3.5a1 1 0 0 1 1 1c0 1.25.2 2.45.57 3.57a1 1 0 0 1-.25 1z"/></svg>
    +1 555 010 0199
  </div>
  <div class="item" style="left:308px">
    <svg width="16" height="13" viewBox="0 0 24 18"><path d="M1 1h22v16H1z" fill="none" stroke="#fff" stroke-width="2"/><path d="M1 1l11 9 11-9" fill="none" stroke="#fff" stroke-width="2"/></svg>
    info@ridgelinehaulage.com
  </div>
  <div class="dots" aria-label="Social links"><span></span><span></span><span></span></div>
</div>

<!-- header -->
<div class="abs header">
  <div class="brand"><div class="words"><span>Ridgeline</span><span>Haulage</span></div><span class="mark"></span></div>
  <span class="nav" style="left:487px">Home</span>
  <span class="nav" style="left:568px">Trucking Services</span>
  <span class="nav" style="left:726px">About</span>
  <span class="nav" style="left:804px">Contact Us</span>
  <div class="login">
    <svg width="14" height="15" viewBox="0 0 24 24" fill="#fff"><circle cx="12" cy="7" r="5"/><path d="M2 23c0-6 4.5-9 10-9s10 3 10 9z"/></svg>
    LOGIN
  </div>
</div>

<!-- hero -->
<div class="abs hero" role="img" aria-label="Photo of a dark semi truck with a white trailer on a desert road at sunset">
  <svg class="overlay" width="1200" height="559" viewBox="0 0 1200 559">
    <polygon points="0,0 395,0 810,0 330,559 0,559" fill="#d8231f" opacity=".82"/>
    <polygon points="395,0 810,0 300,559 270,559" fill="#e31e24" opacity=".7"/>
    <polygon points="0,0 110,80 0,150" fill="#1f82bf"/>
  </svg>
  <div class="abs head-font welcome">Welcome to</div>
  <h1 class="abs head-font">Ridgeline<br>Haulage</h1>
  <div class="abs cta">Get Started</div>
</div>

<!-- services -->
<h2 class="abs head-font section-title" style="top:766px">Our Services</h2>
<p class="abs lead" style="top:826px">Lorem ipsum dolor sit amet, consectetur adipiscing elit, sed do eiusmod tempor incididunt ut labore et dolore magna aliqua. Quis ipsum suspendisse ultrices gravida. Risus commodo viverra maecenas accumsan lacus vel facilisis.</p>

<div class="abs card" style="left:108px;top:936px;width:235px;height:320px">
  <div class="icon"><svg width="38" height="34" viewBox="0 0 38 34" fill="none" stroke="#fff" stroke-width="2"><rect x="3" y="6" width="32" height="24" rx="2"/><path d="M3 14h32"/><circle cx="11" cy="21" r="2"/><circle cx="24" cy="24" r="2"/></svg></div>
  <h3 style="top:152px">Dirt</h3>
  <p style="top:186px">Lorem ipsum dolor sit amet, consectetur adipiscing elit, sed do eiusmod tempor incididunt ut labore</p>
</div>

<div class="abs card active" style="left:358px;top:936px;width:235px;height:337px">
  <div class="icon"><svg width="40" height="40" viewBox="0 0 40 40" fill="none" stroke="#fff" stroke-width="2"><path d="M12 8c8-2 14 4 12 12s-10 12-14 8-6-18 2-20z"/><path d="M24 14c6 0 10 4 8 10"/></svg></div>
  <h3 style="top:162px">Gravel</h3>
  <p style="top:196px;line-height:24px">Lorem ipsum dolor sit amet, consectetur adipiscing elit, sed do</p>
  <div class="more" style="top:290px">Learn More ➔</div>
</div>

<div class="abs card" style="left:608px;top:936px;width:235px;height:320px">
  <div class="icon"><svg width="42" height="30" viewBox="0 0 42 30" fill="none" stroke="#fff" stroke-width="2"><path d="M4 24c10-2 16-10 34-8"/><path d="M6 16c8 0 14-8 24-6"/><path d="M10 8l6 2"/></svg></div>
  <h3 style="top:152px">Landscape Bark</h3>
  <p style="top:186px">Lorem ipsum dolor sit amet, consectetur adipiscing elit, sed do eiusmod tempor incididunt ut labore</p>
</div>

<div class="abs card" style="left:857px;top:936px;width:236px;height:320px">
  <div class="icon"><svg width="40" height="36" viewBox="0 0 40 36" fill="none" stroke="#fff" stroke-width="2"><path d="M20 3L37 12 20 21 3 12z"/><path d="M3 18l17 9 17-9"/><path d="M3 24l17 9 17-9"/></svg></div>
  <h3 style="top:152px">Landscape<br>Materials</h3>
  <p style="top:212px">Lorem ipsum dolor sit amet, consectetur adipiscing elit, sed do eiusmod</p>
</div>

<!-- about -->
<div class="abs about-band"></div>
<svg class="abs" style="left:0;top:1364px" width="650" height="490" viewBox="0 0 650 490" role="img" aria-label="Photo of a gloved hand scattering bark mulch over a garden bed">
  <defs><linearGradient id="mulch" x1="0" y1="0" x2="0" y2="1"><stop offset="0" stop-color="#6f8a6a"/><stop offset=".5" stop-color="#7a9b3c"/><stop offset="1" stop-color="#6b3a22"/></linearGradient></defs>
  <polygon points="0,0 650,0 330,490" fill="url(#mulch)"/>
</svg>
<div class="about">
  <h2 class="abs head-font">About Ridgeline Haulage</h2>
  <p class="abs">Lorem ipsum dolor sit amet, consectetur adipiscing elit, sed do eiusmod tempor incididunt ut labore et dolore magna aliqua. Quis ipsum suspendisse ultrices gravida. Risus commodo viverra maecenas accumsan lacus vel facilisis. Lorem ipsum dolor sit amet, consectetur adipiscing elit, sed do eiusmod tempor incididunt ut labore et dolore magna aliqua. Quis ipsum suspendisse ultrices gravida. Risus commodo viverra maecenas accumsan lacus vel facilisis. Lorem ipsum dolor sit amet, consectetur adipiscing elit, sed do eiusmod tempor incididunt ut labore et dolore magna aliqua. Quis ipsum suspendisse ultrices gravida. Risus commodo viverra maecenas accumsan lacus vel facilisis. Lorem ipsum dolor</p>
  <div class="abs btn-red" style="left:622px;top:1787px;width:160px;height:51px;border-radius:26px">Learn More</div>
</div>

<!-- testimonials -->
<h2 class="abs head-font section-title" style="top:1996px">Client Testimonial</h2>
<div class="abs arrow" style="left:38px;border:2px solid var(--blue-dark)"><svg width="8" height="12" viewBox="0 0 8 12"><path d="M6 1L1 6l5 5" fill="none" stroke="#1b5f8f" stroke-width="2"/></svg></div>
<div class="abs arrow" style="left:1123px;background:var(--blue)"><svg width="8" height="12" viewBox="0 0 8 12"><path d="M2 1l5 5-5 5" fill="none" stroke="#fff" stroke-width="2"/></svg></div>

<div class="abs quote" style="left:169px">
  <div class="qmark">“</div>
  <h4>Lorem ipsum dolor sit amet, consectetur</h4>
  <p>Lorem ipsum dolor sit amet, consectetur adipiscing elit, sed do eiusmod tempor incididunt ut labore et dolore magna aliqua.</p>
  <div class="who"><div class="avatar" role="img" aria-label="Client portrait"></div><div><div class="name">Marlow Pennick</div><div class="role">Lorem Ipsum</div></div></div>
</div>
<div class="abs quote" style="left:615px">
  <div class="qmark">“</div>
  <h4>Lorem ipsum dolor sit amet, consectetur</h4>
  <p>Lorem ipsum dolor sit amet, consectetur adipiscing elit, sed do eiusmod tempor incididunt ut labore et dolore magna aliqua.</p>
  <div class="who"><div class="avatar" role="img" aria-label="Client portrait"></div><div><div class="name">Marlow Pennick</div><div class="role">Lorem Ipsum</div></div></div>
</div>

<!-- contact -->
<div class="abs contact-bg"></div>
<h2 class="abs head-font section-title" style="top:2578px">Contact Us</h2>
<p class="abs lead" style="top:2640px;left:310px;width:580px">Lorem ipsum dolor sit amet, consectetur adipiscing elit, sed do eiusmod tempor incididunt ut labore et dolore magna aliqua.</p>
<div class="abs field" style="left:110px"><svg width="14" height="14" viewBox="0 0 24 24" fill="none" stroke="#666" stroke-width="2"><circle cx="12" cy="7" r="5"/><path d="M3 23c0-6 4-9 9-9s9 3 9 9"/></svg>Name</div>
<div class="abs field" style="left:442px"><svg width="15" height="12" viewBox="0 0 24 18" fill="none" stroke="#666" stroke-width="2"><path d="M1 1h22v16H1z"/><path d="M1 1l11 9 11-9"/></svg>Email</div>
<div class="abs field" style="left:773px"><svg width="14" height="14" viewBox="0 0 24 24" fill="none" stroke="#666" stroke-width="2"><path d="M6.6 10.8a15.1 15.1 0 0 0 6.6 6.6l2.2-2.2 5.6 1.5V21A17 17 0 0 1 3 4h4.5l1.4 5z"/></svg>Phone</div>
<div class="abs field message"><svg width="14" height="14" viewBox="0 0 24 24" fill="none" stroke="#666" stroke-width="2"><path d="M3 4h18v12H9l-5 4v-4H3z"/></svg>Message</div>
<div class="abs btn-red" style="left:521px;top:3015px;width:168px;height:49px;border-radius:25px">Submit</div>

<!-- footer -->
<div class="abs footer">
  <div class="brand" style="left:112px;top:100px;font-size:28px;line-height:27px"><div class="words"><span>Ridgeline</span><span>Haulage</span></div><span class="mark" style="width:26px;height:26px"></span></div>
  <span class="social first" style="left:169px"></span>
  <span class="social" style="left:206px"></span>
  <span class="social" style="left:242px"></span>
  <span class="social" style="left:278px"></span>

  <h5 style="left:396px">Help Link</h5>
  <ul class="links"><li>Terms &amp; Conditions</li><li>Privacy Policy</li><li>About Us</li><li>Support</li></ul>

  <h5 style="left:580px">Contact Us</h5>
  <div class="abs" style="left:582px;top:138px;display:flex;gap:12px">
    <svg width="12" height="16" viewBox="0 0 12 16" fill="#fff"><path d="M6 0a6 6 0 0 1 6 6c0 4-6 10-6 10S0 10 0 6a6 6 0 0 1 6-6zm0 4a2 2 0 1 0 0 4 2 2 0 0 0 0-4z"/></svg>
    <div><div style="font-weight:700;font-size:14px">Main Office</div><div class="small" style="width:190px;margin-top:4px">Lorem ipsum dolor sit amet, consectetur adipiscing elit, sed do eiusmod tempor</div></div>
  </div>
  <div class="abs small" style="left:580px;top:226px;display:flex;gap:12px;align-items:center"><svg width="15" height="12" viewBox="0 0 24 18" fill="#fff"><path d="M0 0h24v18H0z"/><path d="M1 1l11 9 11-9" fill="none" stroke="#151515" stroke-width="2"/></svg>info@ridgelinehaulage.com</div>
  <div class="abs small" style="left:580px;top:257px;display:flex;gap:12px;align-items:center"><svg width="13" height="13" viewBox="0 0 24 24" fill="#fff"><path d="M6.6 10.8a15.1 15.1 0 0 0 6.6 6.6l2.2-2.2 5.6 1.5V21A17 17 0 0 1 3 4h4.5l1.4 5z"/></svg>+1 555 010 0199</div>

  <h5 style="left:812px">Get Our Newsletter</h5>
  <div class="abs" style="left:813px;top:132px;width:278px;height:42px;border:1px solid #555;border-radius:4px;font-size:14px;color:#888;padding:12px 16px">Enter Your Email</div>
  <div class="abs btn-red" style="left:813px;top:186px;width:278px;height:41px;border-radius:4px;font-size:14px">Subscribe Now</div>

  <div class="abs" style="left:110px;top:346px;width:980px;height:1px;background:#2c2c2c"></div>
  <div class="abs" style="left:0;top:386px;width:1200px;text-align:center;font-size:15px">©Copyrights 2023&nbsp; Ridgeline Haulage &nbsp;|&nbsp;&nbsp; All Rights Reserved</div>
</div>

</body>
</html>
```